BUSINESS CARD DESIGN

NAME- DALE VORSKIN
PHONE NUMER - 555- 714-9082
EMAIL- OFFICE@TRV-GROUNDMAKRZ.COM
BACK OF CARD- SPEACIALIZES IN LAND CLEARING, FORESTRY MUCLHING AND EXCAVATION

Contact Information for Business Card

NAME- DALE VORSKIN PHONE NUMER - 555- 714-9082 EMAIL- OFFICE@TRV-GROUNDMAKRZ.COM BACK OF CARD- SPEACIALIZES IN LAND CLEARING , MUCLHING AND EXCAVATION

```html
<!DOCTYPE html>
<html lang="en">
<head>
<meta charset="UTF-8">
<title>Business Card – Dale Vorskin</title>
<link href="https://fonts.googleapis.com/css2?family=Montserrat:wght@500;700&family=Lato:ital,wght@0,400;1,400&family=Roboto+Condensed:wght@500&display=swap" rel="stylesheet">
<style>
  :root {
    --backdrop: #2b2c2e;
    --card-white: #ffffff;
    --card-black: #161718;
    --ink: #111111;
    --muted: #6d6d6d;
    --accent: #f5a800;
    --silver: #d9d9d9;
  }
  html, body {
    margin: 0;
    width: 1200px;
    height: 952px;
    overflow: hidden;
    background: var(--backdrop);
  }
  .stage {
    width: 1200px;
    height: 952px;
    display: flex;
    flex-direction: column;
    align-items: center;
    justify-content: center;
    gap: 40px;
  }
  .card {
    position: relative;
    width: 700px;
    height: 400px;
    box-shadow: 0 10px 30px rgba(0,0,0,.45);
    overflow: hidden;
  }

  /* Front */
  .card-front { background: var(--card-white); }
  .holder {
    position: absolute;
    left: 44px;
    top: 40px;
    font-family: "Montserrat", sans-serif;
  }
  .holder-name {
    margin: 0;
    font-size: 30px;
    font-weight: 500;
    letter-spacing: .5px;
    color: var(--ink);
  }
  .holder-name .surname { color: var(--accent); }
  .holder-title {
    margin: 4px 0 0;
    font-family: "Lato", sans-serif;
    font-style: italic;
    font-size: 15px;
    color: var(--muted);
  }
  .scene-art {
    position: absolute;
    left: 0;
    bottom: 0;
    width: 270px;
    height: 270px;
    background: linear-gradient(160deg, #3a3a3a 0%, #0d0d0d 70%);
    clip-path: polygon(0 10%, 100% 30%, 100% 100%, 0 100%);
  }
  .brand-front {
    position: absolute;
    right: 44px;
    top: 130px;
    display: flex;
    align-items: center;
    gap: 12px;
    font-family: "Montserrat", sans-serif;
    font-weight: 700;
    font-size: 20px;
    color: var(--ink);
  }
  .brand-dot {
    width: 34px;
    height: 34px;
    border-radius: 50%;
    background: var(--ink);
  }
  .contact {
    position: absolute;
    right: 44px;
    bottom: 42px;
    margin: 0;
    padding: 0;
    list-style: none;
    font-family: "Lato", sans-serif;
    font-size: 17px;
    color: var(--muted);
    text-align: right;
  }
  .contact li {
    display: flex;
    justify-content: flex-end;
    align-items: center;
    gap: 10px;
    line-height: 30px;
  }
  .contact .phone { font-size: 19px; color: #555; }
  .contact svg { width: 16px; height: 16px; fill: var(--accent); }

  /* Back */
  .card-back {
    background: var(--card-black);
    display: flex;
    flex-direction: column;
    align-items: center;
    justify-content: center;
  }
  .brand-back {
    display: flex;
    align-items: center;
    gap: 14px;
    font-family: "Montserrat", sans-serif;
    font-weight: 700;
    font-size: 28px;
    color: var(--silver);
  }
  .brand-back .brand-dot { background: var(--silver); width: 44px; height: 44px; }
  .rule {
    width: 460px;
    height: 1px;
    margin: 30px 0 12px;
    background: linear-gradient(90deg, transparent, var(--accent), transparent);
  }
  .services {
    display: flex;
    gap: 28px;
    font-family: "Roboto Condensed", sans-serif;
    font-weight: 500;
    font-size: 16px;
    letter-spacing: .3px;
    color: #f2f2f2;
  }
  .services span::before {
    content: "";
    display: inline-block;
    width: 5px;
    height: 5px;
    margin: 0 8px 3px 0;
    border-radius: 50%;
    background: var(--accent);
  }
  .rule-bottom { margin: 12px 0 0; }
</style>
</head>
<body>
<main class="stage">
  <section class="card card-front">
    <div class="holder">
      <h1 class="holder-name">DALE <span class="surname">VORSKIN</span></h1>
      <p class="holder-title">Managing Director</p>
    </div>
    <div class="scene-art" role="img" aria-label="Black silhouette of palm trees and an excavator"></div>
    <div class="brand-front"><span class="brand-dot"></span>Trevara Ground Makrz LLC</div>
    <ul class="contact">
      <li class="phone">555- 714-9082
        <svg viewBox="0 0 24 24"><path d="M6.6 10.8a15 15 0 0 0 6.6 6.6l2.2-2.2c.3-.3.7-.4 1-.2 1.1.4 2.3.6 3.6.6.6 0 1 .4 1 1V20c0 .6-.4 1-1 1A17 17 0 0 1 3 4c0-.6.4-1 1-1h3.5c.6 0 1 .4 1 1 0 1.3.2 2.5.6 3.6.1.3 0 .7-.2 1z"/></svg>
      </li>
      <li>office@trv-groundmakrz.com
        <svg viewBox="0 0 24 24"><path d="M2 5h20v14H2zM4 7v.5l8 5 8-5V7l-8 5z"/></svg>
      </li>
      <li>www.trv-groundmakrz.com
        <svg viewBox="0 0 24 24"><circle cx="12" cy="12" r="10"/></svg>
      </li>
    </ul>
  </section>

  <section class="card card-back">
    <div class="brand-back"><span class="brand-dot"></span>Trevara Ground Makrz LLC</div>
    <div class="rule"></div>
    <div class="services">
      <span>SPEACIALIZES IN LAND CLEARING</span>
      <span>MUCLHING AND EXCAVATION</span>
    </div>
    <div class="rule rule-bottom"></div>
  </section>
</main>
</body>
</html>
```